Heron Property Inspection business card

I am the principal inspector of Heron Property Inspections. I serve Northern Virginia from Winchester to Arlington.Associate, Federated Guild of Dwelling Examiners (FGDE)Graduate, FGDE Home Inspectors CourseNational Association of Home Inspectors ExamI'd like the business card to look more professional than comical.I pulled the attached picture off the web. I'd like to have something like that or an image of a house as my logo on the cards.

Target Market(s)

Persons who recently purchased a home.

Industry/Entity Type

Business

Contact Information for Business Card

Bob AllenBadger Home Inspections, LLC.4455 River RoadBluemont, Virginia 20135cell: 703-231-6680e-mail: tkmarlow@postvale.net

Font styles to use
Serif
Sans Serif

Requirements
Must have
• I'd like to have a logo, something that identifies me as a home inspector. The attached images are something that I'd like to have incorporated into my business card logo.
Nice to have
• I'd like a sketch of a house and/or a magnifying glass showing a house being inspected. The attached images are used as a suggestion only, I do not own the images.
Should not have
• Gimmicky stuff. I want to appear professional and trustworthy.

```html
<!DOCTYPE html>
<html lang="en">
<head>
<meta charset="utf-8">
<title>Heron Property Inspections – Business Card</title>
<link rel="stylesheet" href="https://fonts.googleapis.com/css2?family=Cinzel:wght@600&family=Noto+Sans:wght@400&display=swap">
<style>
  :root {
    --page-bg: #e6e7e9;
    --card-white: #ffffff;
    --slate: #666768;
    --sky: #35a6de;
    --navy: #243f8c;
    --ink: #3a3a3a;
    --mark-tint: #d7e9f5;
  }
  html, body {
    margin: 0;
    width: 1200px;
    height: 902px;
    overflow: hidden;
    background: var(--page-bg);
  }
  .business-card {
    position: absolute;
    left: 130px;
    top: 183.5px;
    width: 940px;
    height: 535px;
    background: var(--card-white);
    box-shadow: 0 6px 24px rgba(0,0,0,0.18);
    overflow: hidden;
  }
  .card-swoosh {
    position: absolute;
    inset: 0;
    width: 100%;
    height: 100%;
  }
  .swoosh-panel { fill: var(--slate); }
  .swoosh-stripe { fill: var(--sky); }

  .brand-mark {
    position: absolute;
    left: 240px;
    top: 58px;
    width: 140px;
    height: 140px;
    border-radius: 50%;
    background: var(--mark-tint);
  }

  .wordmark {
    position: absolute;
    left: 66px;
    top: 214px;
    font-family: "Cinzel", Georgia, serif;
    font-weight: 600;
    color: var(--navy);
    line-height: 1;
  }
  .wordmark-name { font-size: 42px; letter-spacing: 0.5px; }
  .wordmark-company { font-size: 31px; margin-top: 4px; }

  .person {
    position: absolute;
    left: 66px;
    top: 332px;
    font-family: "Noto Sans", Arial, sans-serif;
  }
  .person-name { font-size: 32px; color: var(--ink); line-height: 1.1; }
  .person-title { font-size: 20px; color: var(--navy); margin-top: 2px; }

  .contact-list {
    position: absolute;
    right: 43px;
    top: 394px;
    margin: 0;
    padding: 0;
    list-style: none;
    font-family: "Noto Sans", Arial, sans-serif;
    font-size: 23px;
    color: var(--card-white);
  }
  .contact-item {
    display: flex;
    align-items: center;
    justify-content: flex-end;
    gap: 10px;
    height: 37px;
  }
  .contact-icon {
    width: 26px;
    height: 26px;
    background: var(--card-white);
    display: block;
  }
  .contact-icon svg { display: block; width: 26px; height: 26px; }
  .icon-stroke { fill: none; stroke: var(--sky); stroke-width: 1.8; }
  .icon-fill { fill: var(--sky); }
</style>
</head>
<body>
  <section class="business-card">
    <svg class="card-swoosh" viewBox="0 0 940 535" preserveAspectRatio="none" aria-hidden="true">
      <path class="swoosh-panel" d="M892,0 L940,0 L940,535 L232,535 C520,458 800,262 892,0 Z"/>
      <path class="swoosh-stripe" d="M858,60 C740,300 430,480 112,537 L146,537 C452,478 752,306 863,66 Z"/>
    </svg>

    <div class="brand-mark" role="img" aria-label="Company logo mark"></div>

    <div class="wordmark">
      <div class="wordmark-name">Tim MarlowHeron</div>
      <div class="wordmark-company">Property Inspections, LLC</div>
    </div>

    <div class="person">
      <div class="person-name">Employee Name</div>
      <div class="person-title">Managing Director</div>
    </div>

    <ul class="contact-list">
      <li class="contact-item">
        <span>703-555-0192</span>
        <span class="contact-icon">
          <svg viewBox="0 0 26 26" aria-hidden="true">
            <rect class="icon-stroke" x="9" y="4" width="8" height="18" rx="1.5"/>
            <rect class="icon-fill" x="10.5" y="7" width="5" height="5"/>
          </svg>
        </span>
      </li>
      <li class="contact-item">
        <span>tkmarlow@postvale.net</span>
        <span class="contact-icon">
          <svg viewBox="0 0 26 26" aria-hidden="true">
            <rect class="icon-fill" x="3" y="6" width="20" height="14"/>
            <path d="M3,6 L13,14 L23,6 M3,20 L10,12 M23,20 L16,12" fill="none" stroke="#ffffff" stroke-width="1.4"/>
          </svg>
        </span>
      </li>
      <li class="contact-item">
        <span>7182 Quarry LaneFernhill, Virginia 20148</span>
        <span class="contact-icon">
          <svg viewBox="0 0 26 26" aria-hidden="true">
            <path class="icon-stroke" d="M13,22 C8,15 7,13 7,10.5 A6,6 0 0 1 19,10.5 C19,13 18,15 13,22 Z"/>
            <circle class="icon-fill" cx="13" cy="10.5" r="2.2"/>
          </svg>
        </span>
      </li>
    </ul>
  </section>
</body>
</html>
```